Harbor Crestline (Business Card Design)

Need business cards designed. Something modern, chic, and sleek. Mabye the back of the card should be the navy blue that is in the logo and then just the logo on the back.

Target Market(s)

Those in the hotel, office, and renovation industry

Contact Information for Business Card

1. Logo 2. Dorian Fenwick 3. CEO/Founder 4. Phone: (833) HarbCre / (833) 427-2731 5. Email: dorian@theharborcrestline.com 6. Website: www.theharborcrestline.com

Font styles to use
Other font styles liked:
• Look at the logo font and base the font for everything else off of that.

Colors
0054AA
0677BA
7BADD7
CADEEF
E8F1F8

Requirements
Must have
• Colors that are associated in the logo
Nice to have
• Sleek modern clean and chic design.

```html
<!DOCTYPE html>
<html lang="en">
<head>
<meta charset="utf-8">
<title>Harbor Crestline — Business Cards</title>
<link rel="stylesheet" href="https://fonts.googleapis.com/css2?family=Montserrat:wght@500;600&family=Open+Sans:wght@400;700&display=swap">
<style>
  :root {
    --navy: #0f1941;
    --navy-line: #0b1335;
    --gold: #cfa64a;
    --white: #ffffff;
    --backdrop: #2a2b30;
  }
  * { margin: 0; padding: 0; box-sizing: border-box; }
  html, body { width: 1200px; height: 947px; overflow: hidden; }
  body {
    background: var(--backdrop);
    display: flex;
    flex-direction: column;
    align-items: center;
    justify-content: center;
    gap: 60px;
  }
  .card {
    position: relative;
    width: 640px;
    height: 366px;
    border-radius: 22px;
    background: var(--navy);
    overflow: hidden;
    box-shadow: 0 18px 40px rgba(0,0,0,0.45);
  }
  .brand {
    display: flex;
    align-items: center;
    gap: 14px;
    font-family: "Montserrat", sans-serif;
    font-weight: 600;
    color: var(--white);
    text-transform: uppercase;
    line-height: 1.15;
  }
  .brand-square { background: var(--gold); flex: none; }
  .card-back .brand {
    position: absolute;
    left: 50%; top: 50%;
    transform: translate(-50%, -50%);
    font-size: 38px;
    letter-spacing: 6px;
    gap: 22px;
  }
  .card-back .brand-square { width: 22px; height: 22px; }
  .card-front .brand {
    position: absolute;
    left: 38px; top: 148px;
    font-size: 19px;
    letter-spacing: 3px;
    gap: 12px;
  }
  .card-front .brand-square { width: 12px; height: 12px; }
  .divider {
    position: absolute;
    left: 262px; top: 100px;
    width: 1.5px; height: 140px;
    background: var(--gold);
  }
  .contact {
    position: absolute;
    left: 288px; top: 92px;
    font-family: "Open Sans", sans-serif;
    color: var(--white);
  }
  .contact-name { font-weight: 700; font-size: 25px; color: var(--gold); line-height: 1.1; }
  .contact-title { font-size: 16px; margin-top: 4px; }
  .contact-list { list-style: none; margin-top: 20px; font-size: 14.5px; }
  .contact-list li { display: flex; align-items: center; gap: 9px; line-height: 23px; }
  .contact-list svg { width: 13px; height: 13px; fill: var(--gold); flex: none; }
  .wave { position: absolute; inset: 0; width: 100%; height: 100%; }
</style>
</head>
<body>

  <section class="card card-back" aria-label="Card back">
    <div class="brand"><span class="brand-square"></span><span>Harbor<br>Crestline</span></div>
  </section>

  <section class="card card-front" aria-label="Card front">
    <svg class="wave" viewBox="0 0 640 366" preserveAspectRatio="none" aria-hidden="true">
      <path d="M0,344 C200,338 390,300 470,250 C530,212 585,196 640,194 L640,366 L0,366 Z" fill="var(--gold)"/>
      <path d="M0,334 C170,328 310,302 400,262" fill="none" stroke="var(--white)" stroke-width="6"/>
      <path d="M470,262 C540,220 590,212 640,210" fill="none" stroke="var(--navy-line)" stroke-width="2"/>
    </svg>

    <div class="brand"><span class="brand-square"></span><span>Harbor<br>Crestline</span></div>
    <div class="divider"></div>

    <div class="contact">
      <p class="contact-name">Dorian Fenwick</p>
      <p class="contact-title">Founder + CEO</p>
      <ul class="contact-list">
        <li><svg viewBox="0 0 24 24"><path d="M6.6 10.8a15.1 15.1 0 0 0 6.6 6.6l2.2-2.2a1 1 0 0 1 1-.25 11.4 11.4 0 0 0 3.6.57 1 1 0 0 1 1 1V20a1 1 0 0 1-1 1A17 17 0 0 1 3 4a1 1 0 0 1 1-1h3.5a1 1 0 0 1 1 1c0 1.25.2 2.45.57 3.57a1 1 0 0 1-.25 1z"/></svg>(833) 427-2731</li>
        <li><svg viewBox="0 0 24 24"><path d="M2 5h20v14H2z M2 5l10 8 10-8" fill="none" stroke="var(--gold)" stroke-width="2"/><path d="M2 5h20l-10 8z"/></svg>dorian@theharborcrestline.com</li>
        <li><svg viewBox="0 0 24 24"><circle cx="12" cy="12" r="10" fill="none" stroke="var(--gold)" stroke-width="2"/><path d="M2 12h20M12 2c3 3 3 17 0 20M12 2c-3 3-3 17 0 20" fill="none" stroke="var(--gold)" stroke-width="1.6"/></svg>www.theharborcrestline.com</li>
      </ul>
    </div>
  </section>

</body>
</html>
```